Velmora Freightway Solutions Business cards

Would like a very unique design catchy but professional for business cards. Please use log provided.Marlon WellsCeo and Founder TransCon Logistix Solutions1-888-913-3225mwells@tlsolutionsus.comwww.tlsolutionsus.com

```html
<!DOCTYPE html>
<html lang="en">
<head>
<meta charset="utf-8">
<title>Velmora Freightway Solutions – Business Cards</title>
<link rel="stylesheet" href="https://fonts.googleapis.com/css2?family=Montserrat:wght@600;700&family=Lato:wght@400&display=swap">
<style>
  :root {
    --brand-blue: #1474c4;
    --brand-red: #ed1c24;
    --paper: #ffffff;
    --ink: #3a3a3a;
    --backdrop: #5b5b5b;
  }
  * { margin: 0; padding: 0; box-sizing: border-box; }
  html, body { width: 1200px; height: 802px; overflow: hidden; }
  body { background: var(--backdrop); position: relative; }

  .card {
    position: absolute;
    top: 274px;
    width: 442px;
    height: 264px;
    box-shadow: 0 3px 6px rgba(0,0,0,0.45);
    overflow: hidden;
  }
  .card--front { left: 136px; background: var(--paper); }
  .card--back  { left: 624px; background: var(--brand-blue); }

  .front__band {
    position: absolute; left: 0; top: 0; bottom: 0; width: 47px;
    background: var(--brand-blue);
  }
  .front__stripe {
    position: absolute; left: 47px; top: 0; bottom: 0; width: 5px;
    background: var(--brand-red);
  }
  .brand-name {
    font-family: "Montserrat", sans-serif;
    font-weight: 700;
    letter-spacing: 0.06em;
    text-transform: uppercase;
    text-align: center;
    line-height: 1.25;
  }
  .front__brand {
    position: absolute; left: 190px; width: 230px; top: 56px;
    color: var(--brand-blue);
    font-size: 17px;
  }
  .person { position: absolute; left: 83px; top: 154px; }
  .person__name {
    font-family: "Montserrat", sans-serif; font-weight: 700;
    font-size: 16px; letter-spacing: 0.03em; text-transform: uppercase;
    color: var(--brand-blue);
  }
  .person__surname { color: var(--brand-red); }
  .person__title {
    font-family: "Lato", sans-serif; font-size: 12.5px; color: var(--ink);
    margin-top: 1px;
  }
  .contact { list-style: none; margin-top: 9px; }
  .contact__item {
    font-family: "Lato", sans-serif; font-size: 12.5px; color: var(--ink);
    display: flex; align-items: center; gap: 5px; height: 16px;
  }
  .contact__icon { width: 10px; height: 10px; fill: var(--brand-blue); flex: none; }

  .back__brand {
    position: absolute; left: 0; right: 0; top: 104px;
    color: var(--paper); font-size: 20px;
  }
  .back__bar {
    position: absolute; left: 0; right: 0; top: 199px; height: 36px;
    background: var(--brand-red);
    display: flex; align-items: center; justify-content: center;
    font-family: "Montserrat", sans-serif; font-weight: 600;
    font-size: 11.5px; letter-spacing: 0.06em; color: var(--paper);
  }
</style>
</head>
<body>
  <section class="card card--front">
    <div class="front__band"></div>
    <div class="front__stripe"></div>
    <div class="brand-name front__brand">Velmora Freightway<br>Solutions</div>
    <div class="person">
      <div class="person__name">Dorian <span class="person__surname">Pike</span></div>
      <div class="person__title">CEO and Founder</div>
      <ul class="contact">
        <li class="contact__item">
          <svg class="contact__icon" viewBox="0 0 10 10"><path d="M1 3.5C1 2 3 1 5 1s4 1 4 2.5L7.5 4.2 6.8 3H3.2L2.5 4.2ZM2 5h6l1 4H1Z"/></svg>
          1-888-470-6158
        </li>
        <li class="contact__item">
          <svg class="contact__icon" viewBox="0 0 10 10"><path d="M0.5 2h9v6h-9Zm0.8 0.8V3L5 5.6 8.7 3v-.2Z"/></svg>
          dpike@vfwayroutes.com
        </li>
        <li class="contact__item">
          <svg class="contact__icon" viewBox="0 0 10 10"><circle cx="5" cy="5" r="4.5"/></svg>
          www.vfwayroutes.com
        </li>
      </ul>
    </div>
  </section>

  <section class="card card--back">
    <div class="brand-name back__brand">Velmora Freightway<br>Solutions</div>
    <div class="back__bar">WWW.VFWAYROUTES.COM</div>
  </section>
</body>
</html>
```